Residential Mortgage Leader needs Wordpress Design

Looking for a home page website design for a client. We develop using the WordPress platform and would prefer the design be at least loosely based on an existing WordPress template. Attached files have many notes from our creative brief with client. The site must be responsive. Approved, basic wireframe attached. There is room for interpretation.

Existing web site: http://www.marisolkettering.example/

The Marisol Kettering Team relies on strong systems to deliver an on-time, done-right, friendly experience. Marisol offers mortgages and refinancing services throughout the United States. She is a successful Brookvale Funding agent who strives to be an active part of her community. She would like to focus the site on her team, rather than just her.

Difference makers...
When you work with the Marisol Kettering team you get a high level of expertise and a friendly experience.

She has amazing credentials. Marisol is widely recognized as a top producer for her company, and has earned a number of awards and honors for her customer service.

Marisol's team is very engaged and enjoys sharing social comments or photos from their community.

Imagery:
* Friendly, warm imagery, preferably of her team or an image to represent her team
* Clean and crisp
* Professional / Experts in mortgage and refinance
* Clean / Good use of white space
Updates

When possible, please use imagery from the DFW area. The client mentioned they would prefer not to see stock images. Thanks.

Amend that- creative use of stock images, however, is fine. A few designs have used stock imagery, but in a well-considered manner.

We added some photos and graphics that are local. We are Dallas / Ft. Worth, Plano, Frisco, Texas. We also added some examples of photos to use for the "In the Community" area. Stock photos of business folks just doesn't fit there. Thanks!

Target Market(s)

They service a lot of builders, but also work with homeowners. Their typical client is usually a woman searching for mortgage services online. She typically has a family and may refer her husband to Marisol's team. Keep in mind, however, they also see a number of other scenarios. Most of their clients are middle to high-end borrowers.

Industry/Entity Type

It Company

Requirements
Must have
• Design should be developed using program such as Photoshop or Fireworks or Illustrator as last preference. Ideally, the design would be based on an existing responsive WordPress theme, which we would customize. You must include the name of the target theme. The footer should include lots of space for disclaimers and legal language. Site navigation should include these choices: "Home, About, Builders, Mortgage Info, Approval, Blog, Contact"
Nice to have
• Blog, social media and photos area. Use of the already approved style prototype with colors and fonts (Lato- a Google font, Times New Roman and Cookie-a decorative Google font). However, we are open to interpretation.
Should not have
• Hard to read fonts or a lack of white space.

```html
<!DOCTYPE html>
<html lang="en">
<head>
<meta charset="utf-8">
<title>Marisol Kettering — Brookvale Funding</title>
<link href="https://fonts.googleapis.com/css2?family=Lato:ital,wght@0,400;0,700;0,900;1,700&family=Open+Sans:wght@400;600&display=swap" rel="stylesheet">
<style>
:root{
  --ink:#333538;
  --muted:#6b6e72;
  --red:#c0221a;
  --dark:#22252b;
  --nav:#333333;
  --footer:#3a3a3a;
  --footer-deep:#2e2e2e;
  --soft:#f4f4f4;
  --line:#dcdcdc;
  --link:#2aa7c9;
}
*{margin:0;padding:0;box-sizing:border-box}
html,body{width:725px;height:1200px;overflow:hidden;background:#fff}
body{position:relative;font-family:'Lato',sans-serif;color:var(--ink)}
.abs{position:absolute}

.topbar{left:0;top:0;width:725px;height:20px;background:var(--dark);font-size:8px;color:#c9c9c9}
.topbar .links{left:81px;top:5px;display:flex;gap:12px}
.topbar .social{right:96px;top:5px;display:flex;gap:5px}
.topbar .social span{width:9px;height:9px;border-radius:50%;background:#c9c9c9;display:block}

.header{left:0;top:20px;width:725px;height:81px;background:#fff}
.brand{left:80px;top:26px}
.brand-name{display:flex;align-items:center;gap:6px;font-size:17px;font-weight:700;color:var(--red)}
.brand-name i{width:12px;height:12px;border-radius:50%;background:var(--red);display:block}
.brand-sub{font-size:7.5px;font-weight:700;color:var(--ink);margin-top:2px}
.contact{right:81px;top:27px;font-size:9px;color:#8a8d90;line-height:14px}
.contact svg{vertical-align:-1px;margin-right:5px}

.nav{left:0;top:101px;width:725px;height:31px;background:var(--nav);display:flex;padding-left:71px}
.nav a{color:#fff;font-size:7.5px;font-weight:700;text-decoration:none;padding:0 13px;line-height:31px;border-right:1px solid #555}
.nav a:last-child{border-right:0}

.hero{left:0;top:132px;width:725px;height:282px;background:linear-gradient(90deg,#fbe7c2 0%,#fae2b4 45%,#f7d79a 100%)}
.hero-photo{left:335px;top:0;width:390px;height:282px;background:radial-gradient(ellipse at 55% 55%,#d98a5a 0%,#e9b06a 35%,#f6d494 70%,rgba(247,215,154,0) 100%)}
.hero h1{left:81px;top:80px;font-size:22.5px;font-weight:400;color:#3c3c3c;letter-spacing:.2px}
.hero h1 b{color:var(--red);font-weight:700}
.hero p{left:81px;top:116px;width:280px;font-size:11.5px;line-height:17px;color:#4a4a4a}
.btn{display:block;font-size:9.5px;color:#fff;text-align:center;border-radius:2px}
.btn-start{left:83px;top:167px;width:87px;height:23px;line-height:23px;background:var(--red);box-shadow:0 2px 0 #7a140f}
.hero .or{left:177px;top:172px;font-size:9.5px;color:#4a4a4a}
.btn-know{left:211px;top:167px;width:87px;height:23px;line-height:23px;background:#4a4a4a;box-shadow:0 2px 0 #222}
.dots{left:82px;top:206px;display:flex;gap:7px}
.dots span{width:9px;height:9px;border-radius:50%;background:#444}
.dots span.on{background:var(--red)}

.pitch{left:0;top:414px;width:725px;height:143px;background:var(--soft);border-top:1px solid #e2e2e2;border-bottom:1px solid #e2e2e2;text-align:center}
.pitch h2{margin-top:22px;font-size:19.5px;font-weight:400;line-height:25px;color:#555}
.pitch h2 em{font-style:normal;color:var(--red)}
.pitch .tabs{position:absolute;left:282px;top:86px;display:flex}
.tab{width:106px;height:27px;line-height:27px;font-size:11px;color:#fff;background:#4a4a4a}
.tab.active{width:92px;background:var(--red)}

.section-title{left:77px;top:578px;width:570px;display:flex;align-items:center;gap:20px;font-size:15px;color:#333}
.section-title::before,.section-title::after{content:"";flex:1;height:1px;background:var(--line)}

.cred{left:67px;top:622px;width:591px;height:185px;background:#fff;box-shadow:0 0 4px rgba(0,0,0,.12)}
.cred-badge{left:329px;top:-10px;width:68px;height:68px;border-radius:50%;background:#fff;box-shadow:0 2px 4px rgba(0,0,0,.12)}
.cred-badge span{position:absolute;left:26px;top:26px;width:16px;height:16px;border-radius:50%;background:var(--red)}
.cred-col{top:0;width:268px}
.cred-col h3{font-size:15.5px;font-weight:700;color:#333;text-align:center;padding:21px 0 7px;border-bottom:1px solid #e6e6e6;margin-bottom:15px}
.cred-col p{font-family:'Open Sans',sans-serif;font-size:8px;line-height:14px;color:#555;margin-bottom:4px}
.cred-col ul{list-style:none;font-family:'Open Sans',sans-serif;font-size:8px;color:#555}
.cred-col li{line-height:17px;padding-left:16px;position:relative}
.cred-col li::before{content:"";position:absolute;left:5px;top:6px;width:5px;height:5px;border-radius:50%;background:var(--red)}
.read{display:block;margin:8px 0 0 5px;font-size:7.5px;font-weight:900;font-style:italic;text-decoration:underline;color:#333}

.col-title{top:834px;font-size:10.5px;color:#333}
.post-icon{left:78px;top:866px;width:29px;height:29px;background:#dd5a1a}
.post-date{left:78px;top:901px;width:29px;text-align:center;font-size:13px;font-style:italic;color:#333;line-height:13px}
.post-date small{display:block;font-size:6px}
.post{left:126px;top:870px;width:134px}
.post h4{font-size:8px;font-weight:700;line-height:11px;color:#333}
.post p{font-family:'Open Sans',sans-serif;font-size:7.5px;line-height:11px;color:#777;margin-top:10px}
.post .more{font-family:'Open Sans',sans-serif;font-size:7.5px;color:#333;margin-top:9px}
.post-rule{left:78px;top:960px;width:181px;height:3px;background:repeating-linear-gradient(90deg,#ddd 0 1px,transparent 1px 2px)}
.tweet{left:278px;width:175px}
.tweet .mark{position:absolute;left:2px;top:4px;width:20px;height:20px;border-radius:50%;background:#2aa7e0}
.tweet .mark.sq{border-radius:2px;background:#3b5998}
.tweet p{margin-left:41px;font-family:'Open Sans',sans-serif;font-size:7.5px;line-height:10.5px;color:#666}
.tweet p a{color:var(--link);text-decoration:none}
.tweet p span{color:#aaa}
.tweet-rule{left:271px;top:922px;width:182px;height:2px;background:#e4e4e4}
.community{left:464px;top:866px;display:grid;grid-template-columns:repeat(4,38px);grid-auto-rows:36px;gap:10px 10px}
.community div{background:linear-gradient(160deg,#c9d3dc,#5d6b78)}

.footer{left:0;top:988px;width:725px;height:164px;background:var(--footer);color:#fff}
.footer h5{position:absolute;top:20px;font-size:11px;font-weight:400}
.agent-photo{left:87px;top:49px;width:80px;height:86px;background:linear-gradient(150deg,#bdbdbd,#5f5f5f);border:2px solid #999}
.agent{left:175px;top:50px;font-size:7px;line-height:10px;color:#9d9d9d}
.agent strong{display:block;font-size:10px;font-weight:400;color:#eee;margin-bottom:5px;line-height:12px}
.fine{font-family:'Open Sans',sans-serif;font-size:6.5px;line-height:10px;color:#8d8d8d}
.select{left:489px;top:98px;width:140px;height:16px;background:#777;font-size:6.5px;color:#eee;padding:4px 6px}
.select::after{content:"";position:absolute;right:6px;top:6px;border:4px solid transparent;border-top-color:#bbb}

.bottombar{left:0;top:1152px;width:725px;height:48px;background:var(--footer-deep)}
.bottombar .legal{left:90px;top:19px;font-size:8px;color:#aaa}
.bottombar .housing{left:536px;top:16px;width:17px;height:15px;background:#eee}
.bottombar .icons{left:563px;top:14px;display:flex;gap:4px}
.bottombar .icons span{width:18px;height:18px;border-radius:50%}
</style>
</head>
<body>

<div class="topbar abs">
  <div class="links abs"><span>Terms</span><span>Contact Us</span><span>◍ Language</span></div>
  <div class="social abs"><span></span><span></span><span></span><span></span></div>
</div>

<header class="header abs">
  <div class="brand abs">
    <div class="brand-name">Brookvale Funding <i></i></div>
    <div class="brand-sub">A Northgate Holdings Company</div>
  </div>
  <div class="contact abs">
    <div><svg width="7" height="6" viewBox="0 0 7 6"><rect width="7" height="6" fill="#777"/><path d="M0 0l3.5 3L7 0" stroke="#fff" fill="none" stroke-width=".8"/></svg>email@example.com</div>
    <div><svg width="7" height="7" viewBox="0 0 7 7"><path d="M1 0l1.6 1.8-.8 1a4 4 0 0 0 1.4 1.4l1-.8L6 5 5 7C2.5 6.5.5 4.5 0 2z" fill="#777"/></svg>+00 (123) 456 78 90</div>
  </div>
</header>

<nav class="nav abs">
  <a>HOME</a><a>ABOUT</a><a>BUILDERS</a><a>MORTAGE INFO</a><a>APPROVAL</a><a>BLOG</a><a>CONTACT</a>
</nav>

<section class="hero abs">
  <div class="hero-photo abs" role="img" aria-label="Joyful woman on a sofa throwing colourful cushions into the air"></div>
  <h1 class="abs">EARNING YOUR <b>BUSINESS</b></h1>
  <p class="abs">The Marisol Kettering Team relies on strong systems to deliver on-time, done-right and friendly experience..</p>
  <a class="btn btn-start abs">Start Here</a>
  <span class="or abs">– Or –</span>
  <a class="btn btn-know abs">Get to Know Us</a>
  <div class="dots abs"><span></span><span class="on"></span><span></span></div>
</section>

<section class="pitch abs">
  <h2><em>MARISOL KETTERING...</em> THE ONLY <em>MORTAGE</em> PROFESSIONAL<br>YOU NEED TO KNOW!</h2>
  <div class="tabs"><div class="tab">PURCHASE</div><div class="tab active">REFINANCE</div></div>
</section>

<div class="section-title abs">OUR CREDENTIALS</div>

<section class="cred abs">
  <div class="cred-col abs" style="left:10px">
    <h3>AWARDS</h3>
    <p>Plusieurs variations de Lorem Ipsum peuvent être trouvées ici ou là, mais la majeure partie d'entre elles a été altérée par l'addition</p>
    <ul>
      <li>On sait depuis longtemps que travailler avec</li>
      <li>Du texte lisible et contenant du sens est source de</li>
      <li>Distractions, et empêche de se concentrer</li>
    </ul>
    <a class="read">Read More</a>
  </div>
  <div class="cred-badge abs"><span></span></div>
  <div class="cred-col abs" style="left:326px">
    <h3>RECOGNITION</h3>
    <p>Le Lorem Ipsum est simplement du faux texte employé dans la composition et la mise en page avant impression. Le Lorem Ipsum</p>
    <ul>
      <li>Contrairement à une opinion répandue,</li>
      <li>Le rendant vieux de 2000 ans. Un professeur du</li>
      <li>Latins les plus obscurs, consectetur, extrait d'un passage du</li>
    </ul>
    <a class="read">Read More</a>
  </div>
</section>

<h4 class="col-title abs" style="left:77px">FROM THE BLOG</h4>
<h4 class="col-title abs" style="left:274px">SOCIAL NEWS</h4>
<h4 class="col-title abs" style="left:462px">IN THE COMMUNITY</h4>

<div class="post-icon abs"><svg width="29" height="29" viewBox="0 0 29 29"><path d="M8 18v-3a6.5 6.5 0 0 1 13 0v3" stroke="#fff" stroke-width="2" fill="none"/><rect x="7" y="16" width="3" height="5" fill="#fff"/><rect x="19" y="16" width="3" height="5" fill="#fff"/></svg></div>
<div class="post-date abs">31<small>01,13</small></div>
<article class="post abs">
  <h4>Contrary to popula beliefloremthe Ipsum is simply</h4>
  <p>Lorem Ipsum is dummy text the printing and typesetting instry. Ipsum has been.Lorem Ipsis sly</p>
  <div class="more">Reda More ...</div>
</article>
<div class="post-rule abs"></div>

<div class="tweet abs" style="top:864px"><span class="mark"></span><p><a>@lena_voss</a> Lorem Ipsum is the dummy text the printing typeset-ting instry Ipsum is has been.Lorem<br><span>3 days ago</span></p></div>
<div class="tweet-rule abs"></div>
<div class="tweet abs" style="top:931px"><span class="mark sq"></span><p><a>@lena_voss</a> Lorem Ipsum is the dummy text the printing typeset-<br><span>3 days ago</span></p></div>

<div class="community abs" role="img" aria-label="Grid of eight community photos of team members">
  <div></div><div></div><div></div><div></div><div></div><div></div><div></div><div></div>
</div>

<footer class="footer abs">
  <h5 style="left:87px">About Marisol Kettering</h5>
  <h5 style="left:303px">Disclaimer</h5>
  <h5 style="left:489px">Language</h5>
  <div class="agent-photo abs" role="img" aria-label="Portrait of Marisol Kettering"></div>
  <div class="agent abs">
    <strong>Branch Manager</strong>
    Office: 214.555.0147<br>Cell: 817.555.0192<br>mkettering@brookvalefunding.example<br>NMLS: 40921<br>4820 Larkspur Plaza, Ste.210<br>Cedar Hollow, TX 75099<br>Directions
  </div>
  <p class="fine abs" style="left:304px;top:50px;width:145px">In accordance with Section 326 of the USA PATRIOT Act of 2001, Brookvale Funding is required to obtain a copy of the documents used in identifying our new account custom-ers. This notice is being provided to you for adequate notice given under this act.</p>
  <p class="fine abs" style="left:489px;top:50px;width:140px">Lorem Ipsum is simply dummy text of the printing and typesetting industry. Lorem Ipsum has been the industry's standard dummy text ever since the 1500s been the</p>
  <div class="select abs">English</div>
</footer>

<div class="bottombar abs">
  <span class="legal abs">Marisol Kettering • Legal</span>
  <span class="housing abs"></span>
  <div class="icons abs"><span style="background:#3aa0cf"></span><span style="background:#3b5da5"></span><span style="background:#e07a1e"></span></div>
</div>

</body>
</html>
```